Brochure Brightwell Hearth Partners

Brochure 12 x 9 tri fold with insert/ Rack card 9x4. Brightwell Hearth Partners 318 Corvane Street Easton, MD 21629410-822-2207AgingAtHomeSolution.com Tag: Devoted to Thoughtful Household Support.
What we do: Home care agency that services higher end Clients Artsy area on the water. Taking care of seniors in their home.

Our story: Opening Brightwell Hearth Partners, Inc. is my way of making a difference in an industry that is dominated by franchises that often have their policies dictated by corporate policy-makers who are unfamiliar with local customs. My goal is to raise the level of non-medical home health care in our area by providing additional, customized training, higher wages for our care-partners and an inclusive workforce in the decision-making process when developing customized care planning for our clients. Through collaboration with the client, their family and care-partners I have learned what issues, concerns and disappointments may arise which enables me to provide a more defined solution for those in need.My goal of providing superior training required locating a nationally recognized curriculum that would serve our clients’ needs. I found the perfect fit with Norla Vance’s, Kindred Pathway Method™ and her Shifting Stones Series™. These programs provide our care-partners with the tools needed to handle the challenges of natural aging and living with Dementia. I was so impressed with these programs, I became a Certified Independent Trainer; one of five in the State of Maryland. There is a bonus for our care-partners who are required to maintain Continuing Education Units - these programs qualify for credit! Improving our industry by providing exemplary care-partners is my goal!I look forward to assisting you with your needs! Dana Prewitt Owner

Services: Companion Care Service - Conversation and Companionship , Meal Preparation, Light House Keeping, Errand Service ,Grocery Shopping ,Incidental Transportation, Laundry & Linen Washing, Medication Reminders, Recreational Activities ,
Personal Care Services: Bathing ,Mobility ,Transferring & Positioning ,Incontinence Care ,Oral Hygiene ,Feeding, Toileting ,Grooming & Dressing, Special Diet Preparation.

Our Commitment to You: Extensive Care-Partner Education - We provide, in addition to state mandated training, eight additional hours of hands-on Dementia training from a Certified, Independent Instructor on the “Kindred Pathway Method” by Norla Vance, a nationally recognized instructor on aging.

Nutrition/Local Chef Inspired Training ;We provide six, two-hour food preparation sessions for our care-partners using local chefs, their recipes and locally grown food.

Meaningful & Engaging Activities - We provide a monthly list with local activities to our care-partners based on our client’s interest and capabilities. Focusing on what our client loved to do in the past.

Home Solutions When Needed; We provide management services to help keep our clients in their homes by working with current contractors or locating new ones to properly maintain a safe-living environment.

About owner: Dana Prewitt, owner of Brightwell Hearth Partners, has earned her certification as an Independent Trainer in the Kindred Pathway; Method (KPM) by Norla Vance, a nationally recognized instructor on natural aging and aging with Dementia. Dana is one of five certified independent trainers in the state of Maryland. All staff will have eight hours of hands on Dementia Kindred Pathway Method training.

On the insert 11x 4.25 want the top to be sticking out of the tri -fold "Dementia Experts . I would like to have shades of each STONE as it progresses
The Shifting STONES(R): The STONES model recognizes the dynamic nature of the human brain and its abilities. Unlike other cognitive models, it acknowledges that everyone’s abilities can change in a moment. Modifying environments, situations, interactions, and expectations will create either supportive positive opportunities or result in distress and a sense of failure. Just as gemstones need different settings and care to show their best characteristics, so do people. Rather than focusing on a person’s loss when there is brain change, seeing individuals as precious, unique, and capable encourages a care partnership and is the core of this model. Providing supportive settings for everyone, including care providers, allows them to use what they have to be their best. The STONES® advocate that everyone living with brain change when given the opportunity will shine. Norla Vance and Kindred Pathway Method

Sapphire ~ True Blue ~ Optimal Cognition, Healthy Brain•
True to self: personal preferences remain basically the same
• Can be flexible in thinking and appreciate multiple perspectives
• Stress/pain/fatigue may trigger Diamond state: back to Sapphire with relief
• Able to suppress and filter personal reactions: chooses effective responses
• Selects from options and can make informed decisions
• Processes well and able to successfully transition
• Aging doesn’t change ability: processing slows, more effort/time/practice needed
My brain is healthy - true blue. If I am aging normally or distressed, it may be hard for me to find words. I can describe what I am thinking so you understand. I may talk to myself because I am giving myself cues and prompts. I can learn new things and change habits, but it takes time and effort. Honoring my choices and preferences, when possible, is important. I need more time to make decisions. Give me the details and let me think about it before you need an answer. I am able to remember plans and information but supports are helpful. I may like specific prompts such as notes, calendars, and reminder calls. Health changes in vision, hearing, balance, coordination, depression, anxiety, pain, or medication may impact my behavior, but my cognitive abilities remain the same.

Diamond ~ Clear and Sharp ~ Routines and Rituals Rule
• Displays many facets: behavior and perspective can shift dramatically
• Prefers the familiar and may resist change: challenged by transitions
• More rigid and self-focused; sees wants as needs, when stressed
• Personal likes/dislikes in relationships/space/belongings etc, become more intense
• Reacts to changes in environment; benefits from familiar; functional/forgiving
• Needs repetition and time to absorb new/different information or routines
• Trusted authority figures can help: reacts better when respect is mutual
My overall cognition is clear and sharp. When happy and supported, I am capable and shine in my abilities. When distressed, I can be cutting and rigid and may see help as a threat. I have trouble seeing other points of view and may become less aware of boundaries or more possessive about my relationships, personal space, and belongings. I have many facets so people see me differently depending on the situation. This can cause conflict among my family, friends, or care team as it’s hard to tell if I am choosing my behavior or truly have limits in my ability. I can socially engage and have good cover skills. People will vary in their awareness of what is happening to me. I want to keep habits and environments as they have always been, even if they are problematic for me or others. I am often focused on the past, personal values, or finances. I will need help to make changes in my life; it’s hard for me. I can be in a Diamond state for reasons other than dementia.

Emerald ~ Green and On the Go With a Purpose ~ Naturally Flawed
• Sees self as able and independent, with limited awareness of changes in ability
• Lives in moments of clarity mixed with periods of loss in logic/reason/perspective
• Understanding and use of language change: vague words and many repeats
• Cues and support help when getting to/from places and doing daily routines
• Awareness of time, place, and situation will not always match current reality
• Strong emotional reactions are triggered by fears, desires, or unmet needs
Needs to know what comes next: seeks guidance and assistance to fill the day
I am flawed; it is part of being a natural emerald. I tend to be focused on what I want or need in this moment and may not be aware of my own safety or changing abilities. I can chat socially, but I typically miss one out of every four words and cannot accurately follow the meaning of longer conversations. I won’t remember the details of our time together, but I will remember how your body language and tone of voice made me feel. I may hide or misplace things and believe someone has taken them. My brain will make up information to fill in the blanks, which makes you think I am lying. If you try to correct me or argue, I may become resentful or suspicious of you. I am not always rational, but I don’t want to be made to feel incompetent. My brain plays tricks on me, taking me to different times and places in my life. When I am struggling, I may tell you, “I want to go home.” To provide the help and assistance I need, you must go with my flow, use a positive, partnered approach, and modify my environment.

Amber ~ Caught in a Moment of Time ~ Caution Required
• Focused on sensation: seeks to satisfy desires and tries to avoid what is disliked
•Environment can drive actions and reactions without awareness of safety
• Visual abilities are limited: focus is on pieces or parts, not the whole picture
• What happens to or around an Amber, may cause strong and surprising reactions
• Enters others’ space and crosses boundaries attempting to meet own needs
• Has periods of intense activity: may be very curious or repetitive with objects or actions
• Care is refused or seen as threatening, due to differences in perspective and ability.
Like a particle trapped in an amber, I am caught in a moment of time. It may surprise you to see how I take in the world around me. I may not know you or see you as a whole person. I react to you based on how you look, sound, move, smell, and respond to me. I like to do simple tasks over and over and may need to repeatedly move and touch, smell, taste, take or tear items apart. While it may exhaust or frustrate you, it soothes me. I don’t recognize danger; you will have to safeguard my environment. I’m intolerant to discomfort because my mouth, hands, feet, and genitalia are highly sensitive due to changes in my nervous system. Therefore, activities like eating, taking medication, mouth care, bathing, dressing, and toileting may distress me. Please notice my reaction and stop if I am resisting. I can’t help myself and one or both of us may get hurt emotionally and/or physically. If this happens, wait a few minutes, connect with me, and try a different approach; possibly substituting one area of focus for another.

Ruby ~ Deep and Strong in Color ~ Others Stop Seeing What is Possible
• Makes use of rhythm: can usually sing, hum, pray, sway, rock, clap, and dance
• When moving can’t stop; when stopped can’t get moving: needs guidance and help
• Big, strong movements are possible, while skilled abilities are being lost
• Danger exists due to limited abilities combined with automatic actions or reactions
• Tends to miss subtle hints, but gets magnified facial expressions and voice rhythms
• Can mimic actions or motions, but will struggle to understand instructions/gestures
• Able to pick up and hold objects, and yet not know what to do with them
As the deep red of a ruby masks detail, my obvious losses make my remaining abilities harder to notice. Although my fine motor skills have become very limited, remember that I am able to move and do simple things with my hands. You will need to anticipate, identify, and respond to all of my needs, even though I may not be aware of them. Plan to create a supportive environment, help with the details of care, and structure my day. Just as a crossing guard directs traffic, you will need to guide my movements and transitions. I can rarely stop or start on my own and switching gears is a challenge. Move with me first, then use your body to show me what you want me to do next, going one step at a time. Palm-beneath-Palm™ assistance helps me to feel safe and secure and to know what to do. Danger is part of my life, due to losses in visual skills, chewing abilities, balance, and coordination. You can reduce the risks to me, but not eliminate them. I can still have moments of joy when you are able to provide what gives me pleasure.

Pearl ~ Hidden Within a Shell ~ Beautiful Moments to Behold
• Will frequently recognize familiar touches, voices, faces, aromas, and tastes• Personhood survives, although all other capabilities are minimal
• Understanding input takes time: go slow and simplify for success
• In care, first get connected by offering comfort then use careful and caring touch
• Changes in the body are profound: weight loss, immobility, systems are failing
• As protective reflexes are lost, breathing, swallowing, and moving will be difficult
Care partners benefit from learning the art of letting go rather than simply giving up
While hidden like a pearl in an oyster shell, I will still have moments when I become alert and responsive. I am near the end of my life. Moments of connection create a sense of wholeness and value between us. Use our time together not just to provide care, but to comfort and connect with me. To help me complete life well, it’s important to honor my personhood when making medical or care decisions; please don’t talk about me as though I am not still here. I respond best to familiar voices and gentle rhythmic movements. I am ruled by reflexes and will startle easily. My brain is losing its ability to control and heal my body. Be prepared to see me having difficulty breathing or swallowing. My body may no longer desire food and drink as I prepare to leave this life. I may not be able to stop living without permission from you. Your greatest gift at this time in my life is to let me know that it is okay to go.

Target Market(s)

Children of seniors, seniors , rehabilitation centers

Requirements
Must have
• Nice photos of Seniors that are happy doing thing they like to do with help (Caregivers)
• Upbeat . Positive
Nice to have
• Processional looking - but very personal, we are taking care of their love ones
Should not have
• Not to feel like a cold hospital or end of life

```html
<!DOCTYPE html>
<html lang="en">
<head>
<meta charset="utf-8">
<title>Brightwell Hearth Partners – Brochure Outside</title>
<link rel="stylesheet" href="https://fonts.googleapis.com/css2?family=Montserrat:wght@500;700;800&family=Open+Sans:wght@400;600;700&family=Playball&display=swap">
<style>
:root{
  --navy:#1f4f8f;
  --blue:#2f74b8;
  --sky:#d9e8f5;
  --gold:#c9a03c;
  --gold-light:#e9d9a8;
  --cream:#f7f1e1;
  --ink:#3b4350;
  --page:#e4e4e4;
  --white:#ffffff;
}
*{box-sizing:border-box;margin:0;padding:0}
html,body{width:826px;height:1200px;overflow:hidden;background:var(--page)}
body{font-family:"Open Sans",sans-serif;color:var(--ink)}
.spread{position:absolute;left:0;top:281px;width:826px;height:638px;display:flex;background:var(--white);box-shadow:0 4px 14px rgba(0,0,0,.18)}
.panel{position:relative;width:275.33px;height:100%;overflow:hidden}
.panel + .panel{border-left:1px solid #eee}

/* left panel */
.services-photo{height:196px;background:linear-gradient(135deg,#e9dcc6 0%,#c7b59b 45%,#9fb6cf 100%)}
.swoosh{position:absolute;left:0;width:100%}
.services-title{margin:14px 0 0 22px;display:inline-block;background:var(--cream);border-left:4px solid var(--gold);padding:2px 14px 2px 10px;font-family:"Playball",cursive;font-size:20px;color:var(--navy)}
.service-group{margin:10px 22px 0}
.service-group h3{font-family:"Montserrat",sans-serif;font-weight:800;font-size:10.5px;color:var(--gold);letter-spacing:.3px;margin-bottom:4px}
.service-group.personal h3{color:var(--blue)}
.service-group ul{list-style:none}
.service-group li{font-size:8.6px;line-height:13px;padding-left:10px;position:relative}
.service-group li::before{content:"";position:absolute;left:0;top:4.5px;width:4px;height:4px;border-radius:50%;background:var(--navy)}
.panel-footer{position:absolute;left:0;bottom:0;width:100%;height:20px;background:var(--gold-light);font-size:7.5px;color:var(--navy);display:flex;align-items:center;justify-content:center;font-weight:600}

/* middle panel */
.middle{background:var(--cream)}
.seal{display:block;margin:22px auto 0}
.about-title{margin:14px auto 0;width:120px;text-align:center;background:var(--navy);color:var(--white);font-family:"Playball",cursive;font-size:16px;border-radius:12px;padding:2px 0}
.about-text{margin:10px 24px 0;font-size:7.6px;line-height:11.5px;text-align:justify}
.brand{display:flex;align-items:center;gap:6px;font-family:"Montserrat",sans-serif;font-weight:700;color:var(--navy)}
.brand-dot{width:10px;height:10px;border-radius:50%;background:var(--gold);flex:none}
.middle .brand{justify-content:center;margin-top:22px;font-size:12.5px}
.touch{margin:14px auto 0;width:100px;text-align:center;background:var(--blue);color:var(--white);font-family:"Montserrat",sans-serif;font-weight:700;font-size:9px;border-radius:10px;padding:4px 0;letter-spacing:.6px}
.contact{margin-top:10px;text-align:center;font-size:8.4px;line-height:13px}
.contact .phone{font-weight:700;color:var(--navy);font-size:10px;margin-top:3px;display:flex;justify-content:center;align-items:center;gap:4px}

/* right panel */
.right .brand{margin:24px 0 0 26px;font-size:13px}
.cover-photo{margin-top:18px;height:228px;background:linear-gradient(160deg,#f1e6d2 0%,#d5c2a2 50%,#a9bfd6 100%)}
.headline{margin:34px 22px 0;font-family:"Montserrat",sans-serif;font-weight:800;text-transform:uppercase}
.headline .lead{display:block;font-size:25px;color:var(--gold);letter-spacing:.5px}
.headline .rest{display:block;font-size:15.5px;line-height:19px;color:var(--blue)}
.tagline{margin:10px 22px 0;font-size:8.4px;line-height:12px;color:var(--ink)}
</style>
</head>
<body>
<main class="spread">

  <section class="panel services">
    <div class="services-photo" role="img" aria-label="Photo of a smiling senior woman with a caregiver at home"></div>
    <svg class="swoosh" style="top:168px" width="276" height="40" viewBox="0 0 276 40" aria-hidden="true">
      <path d="M0 28 Q140 -6 276 18 L276 40 L0 40Z" fill="var(--white)"/>
      <path d="M0 26 Q140 -8 276 16" stroke="var(--gold)" stroke-width="4" fill="none"/>
      <path d="M0 32 Q140 2 276 22" stroke="var(--blue)" stroke-width="2" fill="none"/>
    </svg>
    <h2 class="services-title">Our Services</h2>
    <div class="service-group">
      <h3>COMPANION CARE SERVICE</h3>
      <ul>
        <li>Conversation &amp; Companionship</li>
        <li>Meal Preparation</li>
        <li>Light House Keeping</li>
        <li>Errand Service</li>
        <li>Grocery Shopping</li>
        <li>Incidental Transportation</li>
        <li>Laundry &amp; Linen Washing</li>
        <li>Medication Reminders</li>
        <li>Recreational Activities</li>
      </ul>
    </div>
    <div class="service-group personal">
      <h3>PERSONAL CARE SERVICE</h3>
      <ul>
        <li>Bathing</li>
        <li>Mobility</li>
        <li>Transferring &amp; Positioning</li>
        <li>Incontinence Care</li>
        <li>Oral Hygiene</li>
        <li>Feeding</li>
        <li>Toileting</li>
        <li>Grooming &amp; Dressing</li>
        <li>Special Diet Preparation</li>
      </ul>
    </div>
    <div class="panel-footer">BrightwellHearthPartners.example</div>
  </section>

  <section class="panel middle">
    <svg class="seal" width="88" height="88" viewBox="0 0 88 88" aria-hidden="true">
      <circle cx="44" cy="44" r="42" fill="var(--white)" stroke="var(--navy)" stroke-width="3"/>
      <circle cx="44" cy="44" r="30" fill="var(--sky)" stroke="var(--gold)" stroke-width="3"/>
    </svg>
    <h2 class="about-title">About Owner</h2>
    <p class="about-text">Dana Prewitt, owner of Brightwell Hearth Partners, has earned her certification as an Independent Trainer in the Kindred Pathway Method (KPM) by Norla Vance, a nationally recognized instructor on natural aging and aging with Dementia. Dana is one of five certified independent trainers in the state of Maryland. All staff will have eight hours of hands on Dementia Kindred Pathway Method training.</p>
    <div class="brand"><span class="brand-dot"></span>Brightwell Hearth Partners</div>
    <div class="touch">GET IN TOUCH</div>
    <div class="contact">
      <p>318 Corvane Street</p>
      <p>Easton, MD 21774</p>
      <p class="phone">
        <svg width="9" height="9" viewBox="0 0 24 24" aria-hidden="true"><path fill="var(--navy)" d="M6.6 10.8a15 15 0 0 0 6.6 6.6l2.2-2.2a1 1 0 0 1 1-.25 11.4 11.4 0 0 0 3.6.57 1 1 0 0 1 1 1V20a1 1 0 0 1-1 1A17 17 0 0 1 3 4a1 1 0 0 1 1-1h3.5a1 1 0 0 1 1 1c0 1.25.2 2.45.57 3.57a1 1 0 0 1-.25 1z"/></svg>
        410-555-0148
      </p>
      <p>BrightwellHearthPartners.example</p>
    </div>
    <div class="panel-footer">BrightwellHearthPartners.example</div>
  </section>

  <section class="panel right">
    <div class="brand"><span class="brand-dot"></span>Brightwell Hearth Partners</div>
    <div class="cover-photo" role="img" aria-label="Photo of a happy senior woman hugging her caregiver"></div>
    <svg class="swoosh" style="top:270px" width="276" height="44" viewBox="0 0 276 44" aria-hidden="true">
      <path d="M0 20 Q150 44 276 8 L276 44 L0 44Z" fill="var(--white)"/>
      <path d="M0 18 Q150 42 276 6" stroke="var(--gold)" stroke-width="4" fill="none"/>
      <path d="M0 24 Q150 48 276 12" stroke="var(--blue)" stroke-width="2" fill="none"/>
    </svg>
    <h1 class="headline"><span class="lead">Devoted</span><span class="rest">to Thoughtful Household Support</span></h1>
    <p class="tagline">Trusted care partners helping local seniors live safely, happily and independently in the homes and community they love.</p>
    <div class="panel-footer">BrightwellHearthPartners.example</div>
  </section>

</main>
</body>
</html>
```